Create an awesome website for a medical clinic

This is a new website for a doctor's office. The site should be clean and modern, easy to navigate.

This is a wellness clinic, we want to help our clients have a healthy, active lifestyle. It should be friendly and inviting, and easy for them to call or schedule an appointment.

The site should be responsive and designed using the attached Bootstrap 3 PSD.

We will provide stock photos, until then please use stock photos from:

pixelharbor.com or
framequarry.com (preferred)

Some example sites of clean and modern designs that we like:

https://tulsaspinecare.com/
http://reachpastjoints.com/
http://turninghealthier.com/

Also attached is a temporary logo you can use.

Reason: Thank you everyone for your great designs - we need a little more time so I'm extending the project.

Need extra days to review

Also, the colors in the new logo I just linked to are the final colors of the logo, so feel free to use any complimentary colors to it.

Hi everyone, The boss wants to change the layout of the site a little bit - here's the revised layout: https://www.filecrate.com/s/k9rt31vx2qp84zn/notes%2011_29_2017.pdf?dl=0 And the graphic assets you can use are here: https://www.filecrate.com/s/k9rt31vx2qp84zn/notes%2011_29_2017.pdf?dl=0 Feel free to change the background color of the "topbar", and change the icons of the "why people trust us" if you want, these are just temporary placeholders. Thanks for your patience and hard work!

Target Market(s)

People seeking medical treatment (wellness clinic)

Industry/Entity Type

Doctor

Number of Pages Required

1 page

Font styles to use
Sans Serif

Colors
0592cd
33a6d7
abd037
9bcb3c

Requirements
Must have
• The home page should have: a strong hero image/slideshow, clinic phone number should be prominent and at the top of the page (in the nav), a "what to expect" section (this is like a FAQs section - see attachment), and a strong call to action (a button to call or schedule an appointment).
• The what to expect section is useful so that prospective clients can determine if we're a good fit for them or not. It's a basic, first-step pre-qualification block of information.
• Social media icons which links to our social media profiles should be included.
Nice to have
• - Link to 3 most recent blog entries
• - Testimonials
• - How a multilevel nav menu looks.

```html
<!DOCTYPE html>
<html lang="en">
<head>
<meta charset="utf-8">
<title>Willow Medical Clinic</title>
<link href="https://fonts.googleapis.com/css2?family=Montserrat:wght@400;500;600;700&display=swap" rel="stylesheet">
<style>
:root{
  --blue:#0592cd;
  --blue-light:#33a6d7;
  --green:#9bcb3c;
  --topbar:#f5f5f5;
  --ink:#222;
  --white:#fff;
}
*{box-sizing:border-box;margin:0;padding:0}
html,body{width:1200px;height:1200px;overflow:hidden;background:var(--white);font-family:'Montserrat',sans-serif;color:var(--ink)}
.page{position:relative;width:1200px;height:1200px}

.topbar{position:absolute;top:0;left:0;width:1200px;height:45px;background:var(--topbar)}
.social{position:absolute;left:73px;top:11px;display:flex;align-items:center;gap:7px;font-size:11px;letter-spacing:1.5px;font-weight:500}
.social span{margin-right:12px}
.social i{display:block;width:23px;height:23px;border-radius:50%;background:var(--blue-light);opacity:.75}
.appointment{position:absolute;right:74px;top:0;width:243px;height:45px;background:var(--blue);color:var(--white);font-size:11.5px;font-weight:600;letter-spacing:1.6px;display:flex;align-items:center;justify-content:center;text-decoration:none}

.header{position:absolute;top:45px;left:0;width:1200px;height:99px}
.brand{position:absolute;left:73px;top:20px;display:flex;align-items:center;gap:8px}
.brand-square{width:14px;height:14px;background:var(--green)}
.brand-name{font-size:19px;font-weight:700;color:var(--blue);letter-spacing:.5px;line-height:1.15}
.contact{position:absolute;top:29px;display:flex;gap:17px;align-items:center}
.contact-icon{width:43px;height:43px;background:var(--blue);display:flex;align-items:center;justify-content:center}
.contact-text{font-size:9.5px;letter-spacing:1.3px;line-height:14px}
.contact-text strong{font-size:11px;font-weight:600}
.contact.phone{left:722px}
.contact.address{left:930px;top:27px}

.nav{position:absolute;top:144px;left:0;width:1200px;height:60px;background:var(--blue);display:flex;justify-content:center}
.nav a{color:var(--white);text-decoration:none;font-size:13px;font-weight:500;letter-spacing:1.6px;line-height:60px;padding:0 25.5px}

.hero{position:absolute;top:204px;left:0;width:1200px;height:606px;background:linear-gradient(180deg,#7fa9af 0%,#6d9ea6 28%,#4f6f74 45%,#2c3a3d 62%,#1d2224 100%)}
.hero-caption{position:absolute;left:73px;top:183px;width:359px;height:237px;background:rgba(5,120,170,.62)}
.hero-caption h1{margin-top:42px;text-align:center;color:var(--white);font-size:27px;font-weight:500;letter-spacing:2.2px;line-height:30px}
.dots{position:absolute;left:17px;bottom:16px;display:flex;gap:8px}
.dots i{width:9px;height:9px;border-radius:50%;border:1.5px solid var(--white)}
.dots i.active{background:var(--white)}

.services{position:absolute;top:810px;left:0;width:1200px;height:298px;background:var(--blue)}
.service{position:absolute;top:64px;width:245px;color:var(--white)}
.service h2{font-size:17px;font-weight:600;letter-spacing:2px;margin-bottom:11px}
.service p{width:232px;font-size:11.3px;line-height:20.3px;font-weight:500}
.service a{display:inline-block;margin-top:18px;width:120px;height:35px;border:2px solid var(--white);border-radius:18px;color:var(--white);text-decoration:none;font-size:10.5px;font-weight:600;letter-spacing:1.5px;text-align:center;line-height:31px}

.intro{position:absolute;top:1108px;left:0;width:1200px;height:92px}
.intro h2{position:absolute;left:72px;top:44px;font-size:29px;font-weight:500;letter-spacing:3.2px;line-height:30px;width:400px}
.intro-photo{position:absolute;left:685px;top:0;width:515px;height:92px;background:linear-gradient(90deg,#d9dde0 0%,#aeb6bc 50%,#9a7555 75%,#c9d0d4 100%)}
</style>
</head>
<body>
<div class="page">

  <div class="topbar">
    <div class="social"><span>FOLLOW US ON SOCIAL MEDIA!</span><i></i><i></i><i></i></div>
    <a class="appointment" href="#">MAKE AN APPOINTMENT</a>
  </div>

  <header class="header">
    <div class="brand">
      <div class="brand-square"></div>
      <div class="brand-name">WILLOW<br>MEDICAL CLINIC</div>
    </div>
    <div class="contact phone">
      <div class="contact-icon">
        <svg width="24" height="28" viewBox="0 0 24 28"><path d="M5 1 L9 1 L11 8 L8 10 C9 15 11 18 14 21 L17 18 L23 21 L22 26 C14 27 3 16 3 4 Z" fill="#fff"/></svg>
      </div>
      <div class="contact-text"><strong>(555) 410-2736</strong><br>FAX: (555) 410-2790</div>
    </div>
    <div class="contact address">
      <div class="contact-icon">
        <svg width="22" height="30" viewBox="0 0 22 30"><path d="M11 1 C5 1 1 5 1 11 C1 18 11 29 11 29 C11 29 21 18 21 11 C21 5 17 1 11 1 Z" fill="#fff"/><circle cx="11" cy="11" r="4" fill="#0592cd"/></svg>
      </div>
      <div class="contact-text"><strong>UNIT 204, FLOOR 2</strong><br>48 LINDEN GROVE ROAD<br>RIVERTON, FL 30415</div>
    </div>
  </header>

  <nav class="nav">
    <a href="#">HOME</a><a href="#">ABOUT US</a><a href="#">FOR PARENTS</a><a href="#">FOR PROFESSIONALS</a><a href="#">FOR TEENS</a><a href="#">BLOG</a><a href="#">CONTACT US</a>
  </nav>

  <section class="hero" role="img" aria-label="Older man reading a book on a bench beside a misty lake with mountains">
    <div class="hero-caption">
      <h1>We specialise in<br>many areas,<br>find the right<br>clinic for you &amp;<br>your family.</h1>
      <div class="dots"><i class="active"></i><i></i><i></i></div>
    </div>
  </section>

  <section class="services">
    <div class="service" style="left:75px">
      <h2>Selective Placement</h2>
      <p>Lorem ipsum dolor sit amet, consec tetur adipiscing elit. Fusce ornare, turpis vel molestie euismod, lacus ipsum auctor nunc, sed finibus nibh tellus at augue.</p>
      <a href="#">READ MORE</a>
    </div>
    <div class="service" style="left:349px">
      <h2>Selective Placement</h2>
      <p>Lorem ipsum dolor sit amet, consec tetur adipiscing elit. Fusce ornare, turpis vel molestie euismod, lacus ipsum auctor nunc, sed finibus nibh tellus at augue.</p>
      <a href="#">READ MORE</a>
    </div>
    <div class="service" style="left:623px">
      <h2>Selective Placement</h2>
      <p>Lorem ipsum dolor sit amet, consec tetur adipiscing elit. Fusce ornare, turpis vel molestie euismod, lacus ipsum auctor nunc, sed finibus nibh tellus at augue.</p>
      <a href="#">READ MORE</a>
    </div>
    <div class="service" style="left:896px">
      <h2>Selective Placement</h2>
      <p>Lorem ipsum dolor sit amet, consec tetur adipiscing elit. Fusce ornare, turpis vel molestie euismod, lacus ipsum auctor nunc, sed finibus nibh tellus at augue.</p>
      <a href="#">READ MORE</a>
    </div>
  </section>

  <section class="intro">
    <h2>WHAT IS THE RIGHT CLINIC FOR YOU?</h2>
    <div class="intro-photo" role="img" aria-label="Woman with long auburn hair in a bright setting"></div>
  </section>

</div>
</body>
</html>
```